Label design for organic saffron, saffron and herbal syrup

We cultivate saffron, Damszen roses, flowers and herbs. We would need a recognizable outfit (label) for our products. Theoretically (and practically) we have "converted" the family coat of arms into a kind of LOGO. I would send this in the attachment. It would be nice if - in one way or another - this LOGO / coat of arms could be used (certainly with other colors). For some time we have played with the idea of changing the second part of the family name "Wallmoser" (in German .... greuth sounds similar to Kraut / herb [English]) .... eg Wallmoser's saffron syrup into the labeling.
Our products are primarily syrups, currently herbal syrup and saffron syrup. Here the first problem arises, the only bottles / caps that are actually approved for syrup filling (hot filling) are appallingly ugly (see attachment), the only possibility of "sprucing up" is to use so-called "shrink sleeves" (here we need a diameter of 31 and a length of about 40), the colors of which are also limited. Besides the syrup, we sell saffron as a spice and various herbal mixtures (see appendix current packaging saffron). Our quantities are small (syrup 200ml-330ml), saffron in the gram range.
We also need quasi the back of the labeling (this should be able to be redefined per charge) .... Batch 1 (with small quantity has eg more of herb xy than the next batch or the saffron syrup with batch xy needs more / less saffron). In addition, we are certified organic (for this reason, the reverse side would also have to contain all the requirements of organic labeling) [see attachment].
We do not really want to address a specific clientele. Maybe just people who want to taste, enjoy, mix drinks, cook .... (and - unfortunately - don't like Corvel syrup :-) and want to pay a bit more, or find our saffron or herbs better than others) .
In summary
- Strong recognition value (possibly inclusion of "coat of arms", color variable ... although I personally don't like yellow that much)
- Saffron syrup (the color of the saffron syrup is yellow / golden-yellow-light orange, in a transparent ugly bottle)
- Herbal syrup (color variable from blue / green / brown / red elements, in transparent ugly bottle)
Saffron and other herbs (very small containers, type of container not yet fixed)
Regarding a potential "style" I can unfortunately give little information. On the one hand, I am in love with minimalism, on the other hand, I find the translucent, cryptic, implied enormously attractive and sometimes even the "overloaded" colorful has its charm. I think that all in all, it just has to be coherent, and then it will be good.
Requirements
Must have
- Integration of Code of Arms, modifiable for different products

```html
<!DOCTYPE html>
<html lang="en">
<head>
<meta charset="utf-8">
<title>Wallmoser's Herbal Syrup – Label</title>
<link rel="stylesheet" href="https://fonts.googleapis.com/css2?family=PT+Sans:wght@700&family=Yellowtail&family=Open+Sans:wght@400&display=swap">
<style>
  :root {
    --backdrop: #7a7b80;
    --label-green: #1f8f4e;
    --label-green-dark: #0d6a45;
    --ornament-green: #6cc04a;
    --frame-navy: #2e3192;
    --frame-maroon: #6b1d4a;
    --window-light: #fbfdf2;
    --window-mid: #c9e05a;
    --window-edge: #8cc85a;
    --ink-navy: #2e3192;
    --ink-red: #e0262f;
    --band-purple: #8e2f9e;
    --volume-purple: #7b2c8f;
    --leaf-green: #2f9a3a;
  }
  html, body {
    margin: 0;
    padding: 0;
    width: 1200px;
    height: 1200px;
    overflow: hidden;
    background: var(--backdrop);
  }
  .label {
    position: absolute;
    left: 293px;
    top: 96px;
    width: 614px;
    height: 1008px;
    display: block;
  }
  .brand-name {
    font-family: "PT Sans", sans-serif;
    font-weight: 700;
    fill: var(--ink-navy);
  }
  .product-script {
    font-family: "Yellowtail", cursive;
  }
  .product-script .shadow { fill: var(--ink-red); }
  .product-script .face { fill: var(--ink-navy); }
  .volume {
    font-family: "Open Sans", sans-serif;
    font-weight: 400;
    fill: var(--volume-purple);
  }
</style>
</head>
<body>
<svg class="label" viewBox="1030 405 722 1185" xmlns="http://www.w3.org/2000/svg">
  <defs>
    <linearGradient id="outer-fill" x1="0" y1="0" x2="1" y2="0">
      <stop offset="0" stop-color="var(--label-green-dark)"/>
      <stop offset="0.5" stop-color="var(--label-green)"/>
      <stop offset="1" stop-color="var(--label-green-dark)"/>
    </linearGradient>
    <radialGradient id="window-fill" cx="0.5" cy="0.55" r="0.6">
      <stop offset="0" stop-color="var(--window-light)"/>
      <stop offset="0.4" stop-color="var(--window-mid)"/>
      <stop offset="1" stop-color="var(--window-edge)"/>
    </radialGradient>
    <radialGradient id="leaf-fill" cx="0.5" cy="0.5" r="0.5">
      <stop offset="0" stop-color="var(--leaf-green)" stop-opacity="0.9"/>
      <stop offset="1" stop-color="var(--leaf-green)" stop-opacity="0"/>
    </radialGradient>
    <radialGradient id="ornament-fill" cx="0.5" cy="0.5" r="0.5">
      <stop offset="0" stop-color="var(--ornament-green)" stop-opacity="0.85"/>
      <stop offset="1" stop-color="var(--ornament-green)" stop-opacity="0"/>
    </radialGradient>
  </defs>

  <path class="label-body" fill="url(#outer-fill)"
        d="M1080,525 L1190,525 Q1220,468 1290,440 Q1390,405 1490,440 Q1560,468 1590,525 L1700,525 Q1750,525 1750,575 L1750,1530 Q1750,1585 1695,1585 L1087,1585 Q1032,1585 1032,1530 L1032,575 Q1032,525 1080,525 Z"/>

  <g class="side-band">
    <rect x="1032" y="1338" width="70" height="8" fill="#ffffff"/>
    <rect x="1032" y="1350" width="70" height="34" fill="var(--band-purple)"/>
    <rect x="1032" y="1388" width="70" height="8" fill="#ffffff"/>
    <rect x="1684" y="1338" width="66" height="8" fill="#ffffff"/>
    <rect x="1684" y="1350" width="66" height="34" fill="var(--band-purple)"/>
    <rect x="1684" y="1388" width="66" height="8" fill="#ffffff"/>
  </g>

  <g role="img" aria-label="Light green scroll ornaments around the border">
    <ellipse cx="1150" cy="560" rx="110" ry="60" fill="url(#ornament-fill)"/>
    <ellipse cx="1630" cy="560" rx="110" ry="60" fill="url(#ornament-fill)"/>
    <ellipse cx="1395" cy="470" rx="120" ry="40" fill="url(#ornament-fill)"/>
    <ellipse cx="1085" cy="900" rx="45" ry="260" fill="url(#ornament-fill)"/>
    <ellipse cx="1697" cy="900" rx="45" ry="260" fill="url(#ornament-fill)"/>
  </g>

  <g class="window">
    <path d="M1195,1225 L1195,1172 Q1140,1150 1140,1080 L1140,780 Q1140,700 1190,668 Q1202,600 1270,580 Q1320,522 1390,515 Q1460,522 1510,580 Q1578,600 1590,668 Q1640,700 1640,780 L1640,1080 Q1640,1150 1585,1172 L1585,1225 L1690,1225 L1690,1530 L1095,1530 L1095,1225 Z"
          fill="none" stroke="var(--label-green-dark)" stroke-width="34" stroke-linejoin="round"/>
    <path d="M1195,1225 L1195,1172 Q1140,1150 1140,1080 L1140,780 Q1140,700 1190,668 Q1202,600 1270,580 Q1320,522 1390,515 Q1460,522 1510,580 Q1578,600 1590,668 Q1640,700 1640,780 L1640,1080 Q1640,1150 1585,1172 L1585,1225 L1690,1225 L1690,1530 L1095,1530 L1095,1225 Z"
          fill="none" stroke="var(--frame-navy)" stroke-width="18" stroke-linejoin="round"/>
    <path d="M1195,1225 L1195,1172 Q1140,1150 1140,1080 L1140,780 Q1140,700 1190,668 Q1202,600 1270,580 Q1320,522 1390,515 Q1460,522 1510,580 Q1578,600 1590,668 Q1640,700 1640,780 L1640,1080 Q1640,1150 1585,1172 L1585,1225 L1690,1225 L1690,1530 L1095,1530 L1095,1225 Z"
          fill="url(#window-fill)" stroke="var(--frame-maroon)" stroke-width="7" stroke-linejoin="round"/>
  </g>

  <g class="brand-mark">
    <circle cx="1262" cy="690" r="18" fill="var(--ink-navy)"/>
    <text class="brand-name" x="1292" y="705" font-size="44">Wallmoser</text>
  </g>

  <text class="brand-name" x="1390" y="888" font-size="50" text-anchor="middle" letter-spacing="1">WALLMOSER'S</text>

  <g class="product-script" transform="rotate(-9 1400 1040)">
    <text class="shadow" x="1179" y="1034" font-size="120" textLength="265" lengthAdjust="spacingAndGlyphs">Herbal</text>
    <text class="face" x="1175" y="1030" font-size="120" textLength="265" lengthAdjust="spacingAndGlyphs">Herbal</text>
    <text class="shadow" x="1354" y="1139" font-size="130" textLength="250" lengthAdjust="spacingAndGlyphs">Syrup</text>
    <text class="face" x="1350" y="1135" font-size="130" textLength="250" lengthAdjust="spacingAndGlyphs">Syrup</text>
  </g>

  <ellipse role="img" aria-label="Green leaf sprig illustration" cx="1405" cy="1330" rx="130" ry="150" fill="url(#leaf-fill)"/>

  <g class="cert-badge">
    <circle cx="1178" cy="1440" r="62" fill="#ffffff" stroke="var(--ink-red)" stroke-width="5"/>
    <circle cx="1178" cy="1440" r="28" fill="var(--label-green)"/>
  </g>

  <text class="volume" x="1665" y="1495" font-size="36" text-anchor="end">e 200ml</text>
</svg>
</body>
</html>
```